New Business Card Design for Manufacturing

We are an engineering/manufacturing company that offers Advanced machining/assembly/engineering services, as well as innovative products for the heavy duty engine cooling markets.

We are looking to get a new business card designed that is clean and modern looking, but still fits the wide range of technical/skilled work we do.

- We hope to use this design as the base for other design work in new Presentations, web, and print work.

Industry/Entity Type

Engineering

Contact Information for Business Card

Our preferred color of blue is (RGB) 22/71/159 but can vary slightly from that color. Our content will be our Logo and full company name (Vantrell Forge Works, Inc.), company address, name, job title, phone number with extension, cell number, fax number, website, and email address on the cards.
We'd like the full company name next to the logo, but we are open to other interpretations of that layout.
Preferably, we would like the back side to be clean with just our logo, and the front to contain all of the contact information.

Colors
2f74b4
0355a3
85abd2

Requirements
Must have
• - Logo, company name, needed content - We are open to interpretation beyond that.
• - Standard size business card.
• - Horizontal orientation.
• - Enough space for lengthy names / job titles (for example, a job title could read "Directory of Human Resources" or "V.P. of Governmental Affairs"). We need this to look clean, whether the title be short (CEO) or long (as described above).

```html
<!DOCTYPE html>
<html lang="en">
<head>
<meta charset="utf-8">
<title>Vantrell Forge Works — Business Card</title>
<link rel="stylesheet" href="https://fonts.googleapis.com/css2?family=Oswald:wght@500&family=Lato:wght@400;700;900&display=swap">
<style>
  :root {
    --page-bg: #d6d6d6;
    --card-white: #ffffff;
    --card-grey: #7a8188;
    --brand-blue: #16479f;
    --rule-blue: #2f74b4;
    --ink: #3c3f44;
    --ink-soft: #5d6167;
    --on-grey: #ffffff;
  }
  * { box-sizing: border-box; margin: 0; padding: 0; }
  html, body { width: 1200px; height: 800px; overflow: hidden; }
  body {
    background: var(--page-bg);
    font-family: "Lato", sans-serif;
    display: flex;
    align-items: center;
    justify-content: center;
    gap: 40px;
  }
  .card {
    width: 540px;
    height: 309px;
    position: relative;
    box-shadow: 0 2px 6px rgba(0,0,0,0.18);
  }

  /* Front */
  .card--front { background: var(--card-white); color: var(--ink); }
  .identity {
    position: absolute;
    left: 44px;
    top: 96px;
    width: 210px;
    text-align: right;
  }
  .identity__name {
    font-family: "Oswald", sans-serif;
    font-weight: 500;
    font-size: 38px;
    line-height: 1;
    color: var(--brand-blue);
    letter-spacing: 0.5px;
  }
  .identity__title {
    margin-top: 6px;
    font-size: 9.5px;
    letter-spacing: 0.6px;
    text-transform: uppercase;
    color: var(--ink-soft);
  }
  .divider {
    position: absolute;
    left: 270px;
    top: 78px;
    width: 1.5px;
    height: 78px;
    background: var(--rule-blue);
  }
  .contact-list {
    position: absolute;
    left: 284px;
    top: 74px;
    list-style: none;
    font-size: 12px;
    line-height: 16.5px;
    color: var(--ink);
  }
  .contact-list li { display: flex; align-items: center; gap: 7px; }
  .contact-list svg { width: 8px; height: 8px; fill: var(--brand-blue); flex: none; }
  .address {
    position: absolute;
    left: 44px;
    right: 30px;
    bottom: 46px;
    display: flex;
    align-items: center;
    justify-content: center;
    gap: 8px;
    font-size: 13.5px;
    letter-spacing: 0.3px;
    color: var(--ink);
  }
  .address svg { width: 13px; height: 12px; fill: var(--brand-blue); }

  /* Back */
  .card--back { background: var(--card-grey); color: var(--on-grey); }
  .brand {
    position: absolute;
    left: 52px;
    top: 112px;
    display: flex;
    align-items: center;
    gap: 14px;
  }
  .brand__square {
    width: 46px;
    height: 46px;
    border: 4px solid var(--on-grey);
  }
  .brand__name {
    font-weight: 900;
    font-size: 25px;
    line-height: 1.05;
    text-transform: uppercase;
    letter-spacing: 0.4px;
  }
  .website {
    position: absolute;
    right: 34px;
    bottom: 30px;
    font-size: 12px;
    letter-spacing: 1px;
  }
</style>
</head>
<body>

<section class="card card--front" aria-label="Business card front">
  <div class="identity">
    <h1 class="identity__name">DANIEL HARLOW</h1>
    <p class="identity__title">Directory of Human Resources</p>
  </div>
  <div class="divider"></div>
  <ul class="contact-list">
    <li><svg viewBox="0 0 10 10"><path d="M2 0.5l2 2-1 1.2c.6 1.3 1.5 2.2 2.8 2.8l1.2-1 2 2-1.3 1.8C4 9 1 6 .5 1.8z"/></svg>1234- ext</li>
    <li><svg viewBox="0 0 10 10"><rect x="2.5" y="0" width="5" height="10" rx="1"/></svg>555-014-2837</li>
    <li><svg viewBox="0 0 10 10"><rect x="0" y="3" width="10" height="6" rx="1"/><rect x="2.5" y="0" width="5" height="3"/></svg>(555)014-2838</li>
    <li><svg viewBox="0 0 10 10"><path d="M0 2h10v6H0z M0 2l5 3.5L10 2" stroke="#fff" stroke-width="0.8"/></svg>contact@vantrellforge.com</li>
    <li><svg viewBox="0 0 10 10"><circle cx="5" cy="5" r="5"/><path d="M0 5h10M5 0v10" stroke="#fff" stroke-width="0.7"/></svg>www.VantrellForge.com</li>
  </ul>
  <p class="address">
    <svg viewBox="0 0 13 12"><path d="M6.5 0L13 5.5h-2V12H8V8H5v4H2V5.5H0z"/></svg>
    480 Harlan Ridge Rd. Cedar Falls, OH 44012
  </p>
</section>

<section class="card card--back" aria-label="Business card back">
  <div class="brand">
    <div class="brand__square"></div>
    <p class="brand__name">Vantrell<br>Forge Works, Inc.</p>
  </div>
  <p class="website">www.yourwebsite.com</p>
</section>

</body>
</html>
```